We need letterhead, Business Cards, and envelops designed. We have attached a design of our logo and a sample of letterhead idea that was started but never perfected, it is only an idea for the letterhead if you can design something better we may love that also we are open to change.
We want a design that looks professional in style. we are a non profit trade association in the construction industry. the green color in the attached design represent green building, and we like that. also if you just want to enhance the letterhead sample that we attached that would be fine also.
Thanks and good luck
also the name that should show on the first business cards should be Morgan Feltwick, Director are web address is www.pvtrn.org

```html
<!DOCTYPE html>
<html lang="en">
<head>
<meta charset="utf-8">
<title>PVTRN Stationery Set</title>
<link href="https://fonts.googleapis.com/css2?family=Questrial&display=swap" rel="stylesheet">
<style>
  :root {
    --bg: #e6e6e6;
    --paper: #ffffff;
    --ink: #2b2b2b;
    --muted: #5a5a5a;
    --green: #8cc63f;
    --green-dark: #1f7a3a;
    --charcoal: #2e2e2e;
  }
  * { margin: 0; padding: 0; box-sizing: border-box; }
  html, body { width: 1200px; height: 800px; overflow: hidden; }
  body {
    background: var(--bg);
    font-family: "Questrial", sans-serif;
    color: var(--ink);
    position: relative;
  }
  .sheet { position: absolute; background: var(--paper); box-shadow: 0 2px 6px rgba(0,0,0,.12); overflow: hidden; }

  /* wordmark */
  .wordmark { display: inline-flex; align-items: center; gap: 6px; }
  .wordmark__square { width: 12px; height: 12px; background: var(--green); }
  .wordmark__name { font-family: "Questrial", sans-serif; color: var(--ink); letter-spacing: 1px; line-height: 1; }

  /* letterhead */
  .letterhead { left: 80px; top: 60px; width: 430px; height: 556px; padding: 28px 32px; }
  .letterhead__head { display: flex; align-items: flex-end; gap: 6px; }
  .letterhead__head .wordmark__name { font-size: 30px; }
  .letterhead__head .wordmark__square { width: 18px; height: 18px; }
  .letterhead__rule { flex: 1; height: 4px; margin-bottom: 2px;
    background: linear-gradient(90deg, var(--green-dark), var(--green) 70%, rgba(140,198,63,0)); }
  .letter { margin-top: 30px; font-size: 7.6px; line-height: 1.45; color: var(--muted); }
  .letter p { margin-bottom: 9px; }
  .letter__signer { font-weight: bold; color: var(--ink); margin-bottom: 0 !important; }
  .letterhead__foot { position: absolute; left: 32px; right: 32px; bottom: 26px; font-size: 7px; color: var(--muted); }
  .letterhead__web { text-align: right; font-size: 8px; color: var(--green-dark); margin-bottom: 4px; }
  .letterhead__footrule { height: 2px; background: linear-gradient(90deg, var(--green-dark), var(--green)); margin-bottom: 6px; }
  .letterhead__footinfo { line-height: 1.4; text-transform: uppercase; letter-spacing: .3px; }

  /* envelopes */
  .envelope { left: 570px; width: 560px; height: 220px; }
  .envelope--back { top: 60px; }
  .envelope__band { position: absolute; left: 0; top: 0; bottom: 0; width: 130px; background: var(--green); }
  .envelope__band-foot { position: absolute; left: 0; bottom: 0; width: 130px; height: 30px; background: var(--charcoal);
    color: #fff; font-size: 7px; padding: 11px 12px; }
  .envelope__logo { position: absolute; left: 16px; top: 40px; padding: 6px 10px; background: var(--paper); }
  .envelope__logo .wordmark__name { font-size: 22px; }
  .envelope__logo-rule { position: absolute; left: 16px; top: 80px; width: 118px; height: 2px; background: var(--green-dark); }
  .envelope__return { position: absolute; left: 14px; bottom: 44px; font-size: 6.5px; line-height: 1.5; color: #fff; }

  .envelope--flap { top: 300px; }
  .envelope--flap .envelope__band { width: 200px; }
  .envelope__flap { position: absolute; inset: 0; }
  .envelope__flap-logo { position: absolute; left: 250px; top: 44px; }
  .envelope__flap-logo .wordmark__name { font-size: 26px; }
  .envelope__flap-rule { position: absolute; left: 250px; top: 76px; width: 150px; height: 2px; background: var(--green-dark); }

  /* business cards */
  .card { top: 560px; width: 250px; height: 145px; }
  .card--front { left: 600px; display: flex; flex-direction: column; align-items: center; justify-content: center; }
  .card--front .wordmark__name { font-size: 34px; }
  .card--front .wordmark__square { width: 18px; height: 18px; }
  .card__rule { width: 160px; height: 3px; margin-top: 6px; background: linear-gradient(90deg, var(--green-dark), var(--green)); }
  .card--back { left: 880px; padding: 16px 18px; }
  .card__logo { text-align: right; }
  .card__logo .wordmark__name { font-size: 16px; }
  .card__logo .wordmark__square { width: 8px; height: 8px; }
  .card__name { font-size: 13px; margin-top: 16px; color: var(--ink); }
  .card__role { font-size: 8px; font-weight: bold; color: var(--green-dark); margin-bottom: 8px; }
  .card__contacts { display: flex; justify-content: space-between; font-size: 6.3px; line-height: 1.6; color: var(--muted); }
</style>
</head>
<body>

<section class="sheet letterhead" aria-label="Letterhead">
  <header class="letterhead__head">
    <span class="wordmark"><span class="wordmark__name">PVTRN</span><span class="wordmark__square"></span></span>
    <span class="letterhead__rule"></span>
  </header>
  <div class="letter">
    <p>2250, Quarry Bend Road<br>Sacramento, CA 95814.</p>
    <p>January 20th, 2011</p>
    <p>Mr. Hallorin<br>President, Hallorin Youth Center<br>27 Alder Court<br>Portland, OR 97205</p>
    <p>Dear Mr. Hallorin,</p>
    <p>In the first paragraph, one needs to give a brief introduction of oneself. One should also give reference to the purpose of the letter in brief.
    The second paragraph needs to give the details of the letter and its need. This paragraph is mostly longer than the others and plays the main role in the letter. Keep the sentences short and to the point. Avoid using complex words and sentences.</p>
    <p>The third and last paragraph is the conclusion of the letter and can be kept short.</p>
    <p>Sincerely,</p>
    <p>(this is where the signature of the writer will be placed)</p>
    <p class="letter__signer">Tessa Marwick</p>
    <p>Read more at www.lettercraft-notes.org/formats</p>
  </div>
  <footer class="letterhead__foot">
    <div class="letterhead__web">www.pvtrn.org</div>
    <div class="letterhead__footrule"></div>
    <div class="letterhead__footinfo">Sunday Service: 9:00 AM<br>Map &amp; Directions<br>(916) 555 0147</div>
  </footer>
</section>

<section class="sheet envelope envelope--back" aria-label="Envelope, address side">
  <div class="envelope__band"></div>
  <div class="envelope__logo"><span class="wordmark"><span class="wordmark__name">PVTRN</span><span class="wordmark__square"></span></span></div>
  <div class="envelope__logo-rule"></div>
  <div class="envelope__return">2250 Quarry Bend Road<br>Sacramento, CA 95814<br>(916) 555 0147</div>
  <div class="envelope__band-foot">www.pvtrn.org</div>
</section>

<section class="sheet envelope envelope--flap" aria-label="Envelope, flap side">
  <div class="envelope__band"></div>
  <svg class="envelope__flap" viewBox="0 0 560 220" aria-hidden="true">
    <polygon points="0,0 560,0 560,96 40,96 0,60" fill="none" stroke="#cfcfcf" stroke-width="1.2"/>
    <line x1="0" y1="96" x2="560" y2="96" stroke="#e2e2e2" stroke-width="3"/>
  </svg>
  <div class="envelope__flap-logo"><span class="wordmark"><span class="wordmark__name">PVTRN</span><span class="wordmark__square"></span></span></div>
  <div class="envelope__flap-rule"></div>
</section>

<section class="sheet card card--front" aria-label="Business card, front">
  <span class="wordmark"><span class="wordmark__name">PVTRN</span><span class="wordmark__square"></span></span>
  <span class="card__rule"></span>
</section>

<section class="sheet card card--back" aria-label="Business card, back">
  <div class="card__logo"><span class="wordmark"><span class="wordmark__name">PVTRN</span><span class="wordmark__square"></span></span></div>
  <div class="card__name">Morgan Feltwick</div>
  <div class="card__role">Director</div>
  <div class="card__contacts">
    <div>Address: 2250 Quarry Bend Rd<br>Sacramento, CA 95814<br>Phone: (916) 555 0147</div>
    <div>Fax: (916) 555 0148<br>Email: info@pvtrn.org<br>Web: www.pvtrn.org</div>
  </div>
</section>

</body>
</html>
```